Postcard Design Project A Healthy reminder

Dr.'s Dhelpit and Sirel dunwat. Internal Medicine/Family practice. This postcard will be for our patients that we have not seen in a while. Also we need another postcard (the one your designing) with a different heading for New patient's. Do you offer a price break for that? The only thing we would need to change is the heading. Please let me know. Thank you so much! Also can you use the map on the last postcard and our logo I made? I cant find it. Please feel free to call me or email me.

```html
<!DOCTYPE html>
<html lang="en">
<head>
<meta charset="utf-8">
<title>A Healthy Reminder – Postcard</title>
<link rel="stylesheet" href="https://fonts.googleapis.com/css2?family=Open+Sans:wght@300;400;700;800&family=Titillium+Web:wght@400;600;700&family=Montserrat:ital,wght@0,400;1,400;1,900&display=swap">
<style>
  :root{
    --red:#a80d0d;
    --red-deep:#8e0a0a;
    --charcoal:#262626;
    --paper:#ffffff;
    --mist:#f1f1f1;
    --silver:#bdbdbd;
    --backdrop:#dfe6e8;
    --ink:#1d1d1d;
  }
  *{margin:0;padding:0;box-sizing:border-box}
  html,body{width:1200px;height:891px;overflow:hidden;background:var(--backdrop)}
  .canvas{position:relative;width:1200px;height:891px}
  .card{position:absolute;left:290px;width:620px;height:413px;background:var(--paper);box-shadow:0 4px 14px rgba(0,0,0,.15);overflow:hidden}
  .card-front{top:25px}
  .card-back{top:453px}
  .card svg.art{position:absolute;inset:0}

  /* front */
  .brand{position:absolute;left:40px;top:38px;width:200px;text-align:center;font-family:"Open Sans",sans-serif}
  .brand-name{font-size:15px;font-weight:700;color:var(--ink);display:flex;align-items:center;justify-content:center;gap:7px}
  .brand-mark{width:12px;height:12px;background:var(--red)}
  .brand-tag{margin-top:10px;font-size:7px;font-weight:700;letter-spacing:.6px;color:var(--ink)}
  .headline{position:absolute;left:40px;top:134px;color:#fff;font-family:"Open Sans",sans-serif}
  .headline .lead{font-size:21px;font-weight:300;line-height:1.2}
  .headline .lead b{font-weight:800}
  .headline .big{font-weight:800;line-height:.95;letter-spacing:-.5px}
  .headline .annual{font-size:37px;margin-top:8px}
  .headline .exam{font-size:55px}
  .contact{position:absolute;left:34px;top:295px;color:#fff;font-family:"Titillium Web",sans-serif}
  .contact-row{display:flex;align-items:flex-start;gap:6px}
  .contact .addr{font-size:13px;line-height:1.3}
  .contact .phone{font-size:22px;font-weight:700;margin-top:4px;align-items:center}
  .contact .web{font-size:12px;margin-top:4px;align-items:center}

  /* back */
  .back-title{position:absolute;left:26px;top:14px;font-family:"Montserrat",sans-serif;font-style:italic;color:var(--red);font-size:16px;line-height:1.05}
  .back-title b{font-weight:900}
  .back-title span{font-weight:400;color:var(--ink)}
  .call{position:absolute;left:26px;top:200px;color:#fff;font-family:"Montserrat",sans-serif;font-style:italic;font-weight:900;font-size:23px;line-height:1.02}
  .visit{position:absolute;left:26px;top:290px;color:#fff;font-family:"Montserrat",sans-serif;font-style:italic}
  .visit .label{font-size:8px;font-weight:900;letter-spacing:.5px}
  .visit .url{font-size:10px;margin-top:4px}
  .visit .loc{font-size:13px;margin-top:8px;font-weight:400}
  .visit .corner{font-size:12px;font-weight:900;margin-top:2px}
</style>
</head>
<body>
<div class="canvas">

  <section class="card card-front" aria-label="Postcard front">
    <svg class="art" width="620" height="413" viewBox="0 0 620 413">
      <rect x="0" y="0" width="620" height="120" fill="var(--mist)"/>
      <rect x="0" y="120" width="620" height="165" fill="var(--red)"/>
      <rect x="0" y="285" width="620" height="128" fill="var(--charcoal)"/>
      <path d="M312 0 Q228 200 336 413" fill="none" stroke="var(--silver)" stroke-width="16"/>
      <path d="M322 0 Q238 200 346 413" fill="none" stroke="var(--red)" stroke-width="9"/>
      <path d="M330 0 Q246 200 354 413 L620 413 L620 0 Z" fill="#d9c9b4" role="img" aria-label="Photo: two doctors in white coats reviewing a patient chart in a clinic hallway"/>
      <path d="M330 0 Q246 200 354 413 L620 413 L620 0 Z" fill="url(#hall)"/>
      <defs>
        <linearGradient id="hall" x1="0" y1="0" x2="1" y2="1">
          <stop offset="0" stop-color="#c9a98a" stop-opacity=".6"/>
          <stop offset=".55" stop-color="#ece7df" stop-opacity=".7"/>
          <stop offset="1" stop-color="#b8c2c4" stop-opacity=".6"/>
        </linearGradient>
      </defs>
    </svg>

    <div class="brand">
      <div class="brand-name"><span class="brand-mark"></span>Dhelpit T Dunwat, M.D.</div>
      <div class="brand-tag">A Primary Care Office</div>
    </div>

    <div class="headline">
      <p class="lead">A healthy <b>reminder,</b></p>
      <p class="lead">It is time for your</p>
      <p class="big annual">ANNUAL</p>
      <p class="big exam">EXAM.</p>
    </div>

    <div class="contact">
      <div class="contact-row addr">
        <svg width="10" height="14" viewBox="0 0 10 14"><path d="M5 1a3.5 3.5 0 0 0-3.5 3.5C1.5 7 5 12 5 12s3.5-5 3.5-7.5A3.5 3.5 0 0 0 5 1z" fill="none" stroke="#fff" stroke-width="1.2"/><circle cx="5" cy="4.6" r="1.2" fill="#fff"/></svg>
        <p>4820 N. Calder Avenue Suite 210<br>Marlow, Ca 93410</p>
      </div>
      <div class="contact-row phone">
        <svg width="18" height="18" viewBox="0 0 18 18"><circle cx="9" cy="9" r="8" fill="none" stroke="#fff" stroke-width="1.4"/><path d="M6.2 4.8l1.6 1.9-.9 1.3c.6 1.3 1.6 2.3 2.9 2.9l1.3-.9 1.9 1.6-.9 1.4c-3.5-.3-6.6-3.4-6.9-6.9z" fill="#fff"/></svg>
        <p>(555) 214-6830</p>
      </div>
      <div class="contact-row web">
        <svg width="11" height="11" viewBox="0 0 12 12"><circle cx="6" cy="6" r="5" fill="none" stroke="#fff"/><ellipse cx="6" cy="6" rx="2.2" ry="5" fill="none" stroke="#fff" stroke-width=".8"/><path d="M1 6h10" stroke="#fff" stroke-width=".8"/></svg>
        <p>www.dhelpitdunwatmd.com</p>
      </div>
    </div>
  </section>

  <section class="card card-back" aria-label="Postcard back">
    <svg class="art" width="620" height="413" viewBox="0 0 620 413">
      <defs>
        <clipPath id="panel"><path d="M0 0 L330 0 Q372 230 210 413 L0 413 Z"/></clipPath>
        <linearGradient id="map" x1="0" y1="0" x2="1" y2="0">
          <stop offset="0" stop-color="#cfe6c4"/>
          <stop offset=".5" stop-color="#e9ecee"/>
          <stop offset="1" stop-color="#e2e6ea"/>
        </linearGradient>
      </defs>
      <path d="M338 0 Q380 230 218 413" fill="none" stroke="var(--silver)" stroke-width="14"/>
      <path d="M332 0 Q374 230 212 413" fill="none" stroke="var(--red)" stroke-width="8"/>
      <g clip-path="url(#panel)">
        <rect x="0" y="0" width="400" height="190" fill="var(--paper)"/>
        <rect x="0" y="50" width="400" height="140" fill="url(#map)" role="img" aria-label="Street map showing the office location"/>
        <rect x="0" y="190" width="400" height="78" fill="var(--red)"/>
        <rect x="0" y="268" width="400" height="145" fill="var(--charcoal)"/>
      </g>
      <circle cx="312" cy="236" r="66" fill="var(--red)"/>
      <circle cx="312" cy="236" r="58" fill="#8aa06d" role="img" aria-label="Photo: front entrance of the office building with shrubs"/>
      <rect x="480" y="38" width="90" height="44" fill="none" stroke="#444" stroke-width="1"/>
      <line x1="400" y1="248" x2="575" y2="248" stroke="#444" stroke-width="1"/>
      <line x1="390" y1="280" x2="575" y2="280" stroke="#444" stroke-width="1"/>
      <line x1="380" y1="312" x2="575" y2="312" stroke="#444" stroke-width="1"/>
    </svg>

    <h2 class="back-title"><b>Dr.'s Dhelpit</b> <span>and</span><br><b>Sirel Dunwat</b></h2>

    <p class="call">CALL NOW<br>(555) 214-6830</p>

    <div class="visit">
      <p class="label">VISIT US ON</p>
      <p class="url">www.socialpage.com/doctorsdunwat</p>
      <p class="loc">Located On The</p>
      <p class="corner">SE corner of Calder and Wren.</p>
    </div>
  </section>

</div>
</body>
</html>
```